Creation of a construction/bricklaying business website

Following the template format of "Halloway 7", the following content would need to be included:
1. Landing page with 3 tiles that go to their own pages.
- Landing page to include background photo and description of services offered.
2. 3 tiles to include:
a) "Contact Us For A Free Quote or Friendly Discussion" Form (middle tile)
b) Case Studies and Testimonials
c) Certifications and Professional Membership
- Design logo to be used from previous SketchNestle project. Example of logo attached below, please access full JPG files from our account.

Target Market(s)

Prospective clients seeking construction work (bricklaying speciality)

Industry/Entity Type

Residential Construction

Coding

Coded - Design and coding required

Number of Pages Required

4 page

Font styles to use
Sans Serif

Colors

Designer to choose colors to be used in the design.

Requirements
Must have
• Following the template format of "Halloway 7", the following content would need to be included:
• 1. Landing parent page with 3 tiles that go to the 3 child pages.
• - Landing page to include background photo and description of services offered.
• 2. 3 tiles to include:
• a) "Contact Us For A Free Quote or Friendly Discussion" Form (middle tile)
• b) Case Studies and Testimonials (first tile / left side)
• c) Certifications and Professional Memberships (third tile / right side) (This should include logos of the relevant organisations being displayed. Specifically plain badge shape and the Pillar Seal GQT).
• - Design logo to be used from previous SketchNestle project. Example of logo attached below, please access full JPG files from our account.
Nice to have
• Sleek and modern feel.
• Approachable in terms of how people can contact the company for a quote.
• Traditional pictures to give credibility and comfort around choosing this company.
Should not have
• Cheesy pictures
• Over-complicated
• Simple to use
• Easy URL domain name

```html
<!DOCTYPE html>
<html lang="en">
<head>
<meta charset="utf-8">
<title>R.T.Marlow Construction Ltd</title>
<link href="https://fonts.googleapis.com/css2?family=Didact+Gothic&family=Mulish:wght@400;600;700&display=swap" rel="stylesheet">
<style>
:root{
  --blue:#0b4fa6;
  --blue-dark:#083f86;
  --ink:#222;
  --muted:#3a3a3a;
  --tile:#e8ecec;
  --white:#fff;
}
*{box-sizing:border-box;margin:0;padding:0}
html,body{width:920px;height:1200px;overflow:hidden;background:var(--white)}
body{position:relative;font-family:"Mulish",sans-serif;color:var(--ink)}
.abs{position:absolute}

.hero{left:0;top:0;width:920px;height:315px;
  background:linear-gradient(100deg,#8a8a88 0%,#a9a8a5 35%,#6f6f6d 70%,#8d8b85 100%)}
.hero-shade{left:0;top:0;width:920px;height:315px;background:rgba(40,40,40,.35)}
.contact-chip{display:flex;align-items:center;gap:8px;color:var(--white);font-size:11px;line-height:16px;font-family:"Didact Gothic",sans-serif}
.chip-icon{width:28px;height:28px;border-radius:50%;background:var(--blue);display:flex;align-items:center;justify-content:center;flex:none}
.brand{left:0;width:920px;top:120px;text-align:center;color:var(--white);font-family:"Didact Gothic",sans-serif}
.brand-name{font-size:46px;line-height:50px;letter-spacing:1px}
.brand-sub{font-size:18px;letter-spacing:3px;margin-top:4px}

.nav{left:0;top:315px;width:917px;height:36px;background:var(--blue);display:flex;align-items:center}
.nav a{position:absolute;color:var(--white);text-decoration:none;font-size:11px;font-weight:600;font-family:"Mulish",sans-serif}
.nav a.active{color:#111}

.section-title{left:0;width:920px;top:380px;text-align:center;color:var(--blue);font-family:"Didact Gothic",sans-serif;font-size:22px;font-weight:700;-webkit-text-stroke:.4px var(--blue)}
.intro{left:170px;width:580px;top:422px;text-align:center;font-family:"Didact Gothic",sans-serif;font-size:14.5px;line-height:18px;color:var(--ink);-webkit-text-stroke:.3px var(--ink)}

.service{width:120px;text-align:center}
.service-badge{width:78px;height:78px;margin:0 auto;border-radius:50%;border:3px solid var(--blue);background:radial-gradient(circle at 50% 40%,#fff 0%,#e4e4e4 100%);display:flex;align-items:center;justify-content:center}
.service-shadow{width:64px;height:4px;margin:3px auto 0;border-radius:50%;background:rgba(0,0,0,.08)}
.service-label{margin-top:20px;font-family:"Didact Gothic",sans-serif;font-size:15px;line-height:18px;color:var(--ink);-webkit-text-stroke:.3px var(--ink)}

.copy{left:120px;width:680px;text-align:center;font-size:12px;line-height:18.5px;color:#111}

.tile{top:753px;width:224px;height:209px;text-align:center;padding-top:22px}
.tile.grey{background:var(--tile)}
.tile-icon{height:50px;display:flex;justify-content:center;align-items:center;gap:6px}
.tile-title{margin-top:12px;font-size:11px;font-weight:700;line-height:14.5px;color:#111}
.tile-text{margin:12px 6px 0;font-size:10px;line-height:16.5px;color:var(--muted)}
.tile-link{display:inline-block;margin-top:12px;font-size:11px;font-weight:700;color:var(--blue);text-decoration:none}

.footer{left:0;top:1007px;width:920px;height:193px;background:linear-gradient(160deg,#3a4a55 0%,#2a3640 45%,#4a5656 100%)}
.footer-shade{left:0;top:1007px;width:920px;height:193px;background:rgba(20,30,45,.45)}
.footer-brand{left:0;width:920px;top:1038px;text-align:center;color:var(--white);font-family:"Didact Gothic",sans-serif}
.footer-brand .brand-name{font-size:18px;line-height:20px}
.footer-brand .brand-sub{font-size:7px;letter-spacing:1.5px;margin-top:1px}
.footer-rule{left:124px;top:1147px;width:672px;height:1px;background:rgba(255,255,255,.2)}
.copyright{left:146px;top:1170px;color:var(--white);font-size:10.5px;font-family:"Didact Gothic",sans-serif}
.social{top:1162px;width:24px;height:24px;border-radius:50%;background:var(--white)}
</style>
</head>
<body>

<div class="abs hero" role="img" aria-label="Photo of a builder trowelling plaster onto a block wall"></div>
<div class="abs hero-shade"></div>

<div class="abs contact-chip" style="left:124px;top:14px">
  <span class="chip-icon"><svg width="14" height="14" viewBox="0 0 24 24"><path fill="#fff" d="M6.6 10.8a15 15 0 0 0 6.6 6.6l2.2-2.2c.3-.3.7-.4 1-.2 1.1.4 2.3.6 3.6.6.6 0 1 .4 1 1V20c0 .6-.4 1-1 1A17 17 0 0 1 3 4c0-.6.4-1 1-1h3.5c.6 0 1 .4 1 1 0 1.3.2 2.5.6 3.6.1.3 0 .7-.2 1z"/></svg></span>
  <span>Call Us On<br>555.014.2236</span>
</div>
<div class="abs contact-chip" style="left:626px;top:13px">
  <span class="chip-icon"><svg width="15" height="12" viewBox="0 0 20 14"><rect x="1" y="1" width="18" height="12" fill="none" stroke="#fff" stroke-width="1.6"/><path d="M1 1l9 7 9-7M1 13l7-6M19 13l-7-6" fill="none" stroke="#fff" stroke-width="1.4"/></svg></span>
  <span>Email Us On<br>info@rtmarlowbuild.com</span>
</div>

<div class="abs brand">
  <div class="brand-name">R.T.Marlow</div>
  <div class="brand-sub">CONSTRUCTION LTD</div>
</div>

<nav class="abs nav">
  <a class="active" href="#" style="left:133px">Home</a>
  <a href="#" style="left:200px">Case Studies &amp; Testimonials</a>
  <a href="#" style="left:386px">Contact Us For A Free Quote</a>
  <a href="#" style="left:580px">Certifications &amp; Professional Memberships</a>
</nav>

<h1 class="abs section-title">About Us</h1>
<p class="abs intro">R.T.Marlow Construction Ltd is a construction company that has expertise and experience in the following areas</p>

<div class="abs service" style="left:103px;top:482px">
  <div class="service-badge"><svg width="40" height="36" viewBox="0 0 40 36"><path d="M6 16L20 5l14 11" fill="none" stroke="#333" stroke-width="2.4"/><rect x="10" y="15" width="20" height="14" fill="none" stroke="#333" stroke-width="2"/><rect x="14" y="19" width="5" height="5" fill="#333"/><rect x="22" y="19" width="4" height="10" fill="#333"/><path d="M4 33h32" stroke="#333" stroke-width="1.2"/></svg></div>
  <div class="service-shadow"></div>
  <div class="service-label">Extensions</div>
</div>
<div class="abs service" style="left:221px;top:482px">
  <div class="service-badge"><svg width="40" height="36" viewBox="0 0 40 36"><path d="M4 18L20 4l16 14" fill="none" stroke="#333" stroke-width="3"/><path d="M9 16v16h22V16" fill="none" stroke="#333" stroke-width="2.6"/><rect x="13" y="18" width="6" height="6" fill="#333"/><rect x="22" y="20" width="5" height="12" fill="#333"/></svg></div>
  <div class="service-shadow"></div>
  <div class="service-label">New build /<br>New houses</div>
</div>
<div class="abs service" style="left:346px;top:482px">
  <div class="service-badge"><svg width="46" height="34" viewBox="0 0 46 34" fill="#333"><rect x="2" y="2" width="12" height="5"/><rect x="16" y="2" width="12" height="5"/><rect x="2" y="9" width="42" height="5"/><rect x="2" y="16" width="42" height="5"/><rect x="2" y="23" width="42" height="5"/><rect x="2" y="30" width="42" height="3"/></svg></div>
  <div class="service-shadow"></div>
  <div class="service-label">Garden walls</div>
</div>
<div class="abs service" style="left:458px;top:482px">
  <div class="service-badge"><svg width="44" height="36" viewBox="0 0 44 36" fill="none" stroke="#333" stroke-width="2"><rect x="3" y="3" width="12" height="6"/><rect x="17" y="3" width="12" height="6"/><rect x="3" y="11" width="10" height="6"/><rect x="3" y="19" width="12" height="6"/><rect x="3" y="27" width="10" height="6"/><path d="M18 30l14-16 6 5-14 14z" fill="#333"/></svg></div>
  <div class="service-shadow"></div>
  <div class="service-label">Plastering</div>
</div>
<div class="abs service" style="left:577px;top:482px">
  <div class="service-badge"><svg width="44" height="36" viewBox="0 0 44 36" fill="#333"><rect x="7" y="2" width="3" height="10"/><path d="M4 12h9l-4 12z"/><rect x="16" y="20" width="10" height="4"/><rect x="28" y="20" width="10" height="4"/><rect x="12" y="26" width="10" height="4"/><rect x="24" y="26" width="10" height="4"/><rect x="10" y="32" width="30" height="3"/></svg></div>
  <div class="service-shadow"></div>
  <div class="service-label">Brickwork</div>
</div>
<div class="abs service" style="left:697px;top:482px">
  <div class="service-badge"><svg width="44" height="38" viewBox="0 0 44 38" fill="#333"><rect x="6" y="2" width="10" height="3"/><rect x="10" y="4" width="3" height="18"/><path d="M6 22h11v10a5 5 0 0 1-11 0z"/><path d="M18 36l8-12 6 5 4-3 5 10z"/></svg></div>
  <div class="service-shadow"></div>
  <div class="service-label">Groundworks</div>
</div>

<p class="abs copy" style="top:645px">We pride ourselves on attention to detail, pride in our completed project and client satisfaction. We believe in full transparency and this is reflected in the jobs we quote for you. We break down each step with both labour and materials cost so you can see exactly what you are paying for.</p>
<p class="abs copy" style="top:713px">Feel free to get in touch and we can talk through what you are looking to achieve.</p>

<div class="abs tile grey" style="left:124px">
  <div class="tile-icon"><div role="img" aria-label="Case study document with magnifier and speech bubbles" style="width:72px;height:48px;border-radius:6px;background:linear-gradient(135deg,#dfe6f1,#9fb4d4)"></div></div>
  <div class="tile-title">Case Studies and<br>Testimonials</div>
  <p class="tile-text">Ut wisi enim ad minim veniam, quis nostrud exerci tation ullamcorper suscipit lobortis nisl ut aliquip ex ea commodo consequat.</p>
  <a class="tile-link" href="#">Read More</a>
</div>
<div class="abs tile" style="left:348px">
  <div class="tile-icon"><svg width="46" height="50" viewBox="0 0 46 50"><path d="M8 2h22l10 10v36H8z" fill="#fff" stroke="var(--blue)" stroke-width="2.4"/><path d="M30 2v10h10" fill="none" stroke="var(--blue)" stroke-width="2.4"/><path d="M20 24h14M20 30h14M20 36h14" stroke="var(--blue)" stroke-width="2"/><path d="M3 34l5 9 9-20" fill="none" stroke="#333" stroke-width="3"/></svg></div>
  <div class="tile-title">Contact Us For A<br>Free Quote</div>
  <p class="tile-text">Ut wisi enim ad minim veniam, quis nostrud exerci tation ullamcorper suscipit lobortis nisl ut aliquip ex ea commodo consequat.</p>
  <a class="tile-link" href="#">Contact Us</a>
</div>
<div class="abs tile grey" style="left:572px">
  <div class="tile-icon"><div style="width:29px;height:48px;background:#c8102e"></div><div style="width:29px;height:48px;background:#d81f2a"></div></div>
  <div class="tile-title">Certifications and Professional<br>Memberships</div>
  <p class="tile-text">Ut wisi enim ad minim veniam, quis nostrud exerci tation ullamcorper suscipit lobortis nisl ut aliquip ex ea commodo consequat.</p>
  <a class="tile-link" href="#">Know More</a>
</div>

<div class="abs footer" role="img" aria-label="Aerial photo of a harbour city skyline"></div>
<div class="abs footer-shade"></div>
<div class="abs footer-brand">
  <div class="brand-name">R.T.Marlow</div>
  <div class="brand-sub">CONSTRUCTION LTD</div>
</div>

<div class="abs contact-chip" style="left:146px;top:1090px;gap:17px">
  <span class="chip-icon"><svg width="12" height="15" viewBox="0 0 12 16"><path fill="#fff" d="M6 0a6 6 0 0 0-6 6c0 4.5 6 10 6 10s6-5.5 6-10a6 6 0 0 0-6-6zm0 8.5A2.5 2.5 0 1 1 6 3.5a2.5 2.5 0 0 1 0 5z"/></svg></span>
  <span>Street Name, City Name<br>State Zipcode</span>
</div>
<div class="abs contact-chip" style="left:393px;top:1091px;gap:17px">
  <span class="chip-icon"><svg width="14" height="14" viewBox="0 0 24 24"><path fill="#fff" d="M6.6 10.8a15 15 0 0 0 6.6 6.6l2.2-2.2c.3-.3.7-.4 1-.2 1.1.4 2.3.6 3.6.6.6 0 1 .4 1 1V20c0 .6-.4 1-1 1A17 17 0 0 1 3 4c0-.6.4-1 1-1h3.5c.6 0 1 .4 1 1 0 1.3.2 2.5.6 3.6.1.3 0 .7-.2 1z"/></svg></span>
  <span>Call Us On :<br>555.014.2236</span>
</div>
<div class="abs contact-chip" style="left:597px;top:1090px;gap:17px">
  <span class="chip-icon"><svg width="15" height="12" viewBox="0 0 20 14"><rect x="1" y="1" width="18" height="12" fill="none" stroke="#fff" stroke-width="1.6"/><path d="M1 1l9 7 9-7" fill="none" stroke="#fff" stroke-width="1.4"/></svg></span>
  <span>Email<br>info@rtmarlowbuild.com</span>
</div>

<div class="abs footer-rule"></div>
<div class="abs copyright">Copyright ©2018 R.T.Marlow Construction Ltd. All Rights Reserved.</div>
<div class="abs social" style="left:662px"></div>
<div class="abs social" style="left:689px"></div>
<div class="abs social" style="left:716px"></div>
<div class="abs social" style="left:743px"></div>

</body>
</html>
```